Basic business card

use my newly created logo - and the phrases (Lower Cost of Test & Accelarated New Product Introduction) - and my new email domain / ID - use at conferences / tradeshows

Industry/Entity Type

semiconductor

Contact Information for Business Card

Daniel K Forde, Owner, communicate via Logo - Lower COT - Cost of Test, Accelerated NPI - New Product Introduction, phone +1 555 613 0946, Chandler, Arizona, USA, daniel.forde@qal-vub.com

Font styles to use
Sans Serif

Requirements
Nice to have
• re-use my logo created via Pixel Harbor last August (#7315926)

```html
<!DOCTYPE html>
<html lang="en">
<head>
<meta charset="utf-8">
<title>QAL-VUB Business Card</title>
<link rel="stylesheet" href="https://fonts.googleapis.com/css2?family=Open+Sans:wght@400;600;700&display=swap">
<style>
  :root {
    --stage: #242424;
    --card: #202024;
    --edge: #f39a1e;
    --accent: #f39a1e;
    --text: #ffffff;
    --logo-ink: #3a3b40;
    --deco-a: #2a2f3a;
    --deco-b: #262a32;
  }
  * { margin: 0; padding: 0; box-sizing: border-box; }
  html, body { width: 1200px; height: 780px; overflow: hidden; }
  body {
    background: var(--stage);
    font-family: "Open Sans", sans-serif;
    position: relative;
  }
  .card {
    position: absolute;
    top: 235px;
    width: 540px;
    height: 310px;
    background: var(--card);
    border-bottom: 5px solid var(--edge);
    box-shadow: 0 10px 24px rgba(0,0,0,0.55);
    overflow: hidden;
  }
  .card-front { left: 45px; }
  .card-back { left: 615px; }

  .brand {
    position: absolute;
    inset: 0;
    display: flex;
    align-items: center;
    justify-content: center;
    gap: 16px;
  }
  .brand-mark {
    width: 34px; height: 34px;
    background: var(--logo-ink);
  }
  .brand-name {
    font-weight: 700;
    font-size: 60px;
    letter-spacing: 2px;
    color: var(--logo-ink);
  }

  .backdrop {
    position: absolute;
    left: 30px; top: 40px;
    width: 470px; height: 250px;
    background: linear-gradient(135deg, var(--deco-a), var(--deco-b));
    opacity: 0.8;
  }
  .holder {
    position: absolute;
    left: 40px; top: 118px;
  }
  .holder-name {
    font-size: 30px;
    font-weight: 700;
    color: var(--text);
    line-height: 1.1;
  }
  .holder-name .first { color: var(--accent); }
  .holder-role {
    font-size: 15px;
    color: var(--text);
    margin-top: 4px;
    padding-left: 70px;
  }
  .divider {
    position: absolute;
    left: 300px; top: 78px;
    width: 2px; height: 110px;
    background: var(--text);
  }
  .contacts {
    position: absolute;
    left: 318px; top: 86px;
    list-style: none;
  }
  .contacts li {
    display: flex;
    align-items: center;
    gap: 8px;
    font-size: 14px;
    color: var(--text);
    height: 30px;
  }
  .contacts svg { width: 14px; height: 14px; fill: var(--accent); flex: none; }
  .address {
    position: absolute;
    left: 40px; bottom: 26px;
    font-size: 14.5px;
    color: var(--text);
  }
</style>
</head>
<body>
  <section class="card card-front">
    <div class="brand">
      <span class="brand-mark"></span>
      <span class="brand-name">QAL-VUB</span>
    </div>
  </section>

  <section class="card card-back">
    <div class="backdrop" role="img" aria-label="Faint brand decoration of bars and a sweeping arrow"></div>
    <div class="holder">
      <p class="holder-name"><span class="first">Daniel</span> Forde</p>
      <p class="holder-role">Managing Director</p>
    </div>
    <span class="divider"></span>
    <ul class="contacts">
      <li>
        <svg viewBox="0 0 24 24" aria-hidden="true"><path d="M6.6 10.8a15.1 15.1 0 0 0 6.6 6.6l2.2-2.2a1 1 0 0 1 1-.25 11.4 11.4 0 0 0 3.6.57 1 1 0 0 1 1 1V20a1 1 0 0 1-1 1A17 17 0 0 1 3 4a1 1 0 0 1 1-1h3.5a1 1 0 0 1 1 1c0 1.25.2 2.45.57 3.6a1 1 0 0 1-.25 1z"/></svg>
        +1 555 613 0946
      </li>
      <li>
        <svg viewBox="0 0 24 24" aria-hidden="true"><path d="M3 5h18a1 1 0 0 1 1 1v12a1 1 0 0 1-1 1H3a1 1 0 0 1-1-1V6a1 1 0 0 1 1-1zm9 7.5L20 7H4z"/></svg>
        info@qal-vub.com
      </li>
      <li>
        <svg viewBox="0 0 24 24" aria-hidden="true"><path d="M12 2a10 10 0 1 0 0 20 10 10 0 0 0 0-20zm6.9 6h-3a15 15 0 0 0-1.3-3.9A8 8 0 0 1 18.9 8zM12 4c.8 1.1 1.5 2.5 1.9 4h-3.8c.4-1.5 1.1-2.9 1.9-4zM4.3 14a8 8 0 0 1 0-4h3.4a16 16 0 0 0 0 4zm.8 2h3a15 15 0 0 0 1.3 3.9A8 8 0 0 1 5.1 16zm3-8h-3a8 8 0 0 1 4.3-3.9A15 15 0 0 0 8.1 8zM12 20c-.8-1.1-1.5-2.5-1.9-4h3.8c-.4 1.5-1.1 2.9-1.9 4zm2.3-6H9.7a14 14 0 0 1 0-4h4.6a14 14 0 0 1 0 4zm.3 5.9a15 15 0 0 0 1.3-3.9h3a8 8 0 0 1-4.3 3.9zm1.7-5.9a16 16 0 0 0 0-4h3.4a8 8 0 0 1 0 4z"/></svg>
        www.qal-vub.com
      </li>
    </ul>
    <p class="address">480 Dobson Ridge Rd. Suite 12 Chandler, AZ 85224</p>
  </section>
</body>
</html>
```